Maris Dovey Studio Business Cards

Hi - using the information and logo provided I require a two sided business card designed with the following information. The business card is a 'mini card' 3.5" x 1.25".

Front of card should be the logo attached but inverted (so the background is the peach colour and the logo white).

Back should have these details. If we can't fit the Pictogrum and Friendwall part can we just put the little logos.

Tessa Varnold

Art and Design Consultant
Dealer - Curator - Events - Styling - Creative Sourcing

P: 0438 217 604
E: tessa@marisdoveystudio.example
W: www.marisdoveystudio.example
I (pictogram image please): marisdoveystudio F (Friendwall image please): MarisDoveyAdviser

Target Market(s)

Galleries, artists, art buyers, interior design clients, event managers, creative types

Industry/Entity Type

Business

```html
<!DOCTYPE html>
<html lang="en">
<head>
<meta charset="utf-8">
<title>Maris Dovey Studio – Business Cards</title>
<link rel="stylesheet" href="https://fonts.googleapis.com/css2?family=Tinos:wght@400&display=swap">
<style>
  :root {
    --backdrop: #6b5a4f;
    --card-dark: #171717;
    --card-light: #ffffff;
    --peach: #f2b49a;
    --mark-grey: #8a8a8a;
    --rule-dark: #4a4a4a;
    --rule-light: #d6d6d6;
    --text-white: #ffffff;
    --text-muted: #8c8c8c;
    --text-ink: #1e1e1e;
    --icon-a: #b08a6e;
    --icon-b: #3b5998;
  }
  * { box-sizing: border-box; margin: 0; padding: 0; }
  html, body {
    width: 1200px; height: 960px; overflow: hidden;
    background: var(--backdrop);
    font-family: "Tinos", "Times New Roman", serif;
  }
  .canvas { position: relative; width: 1200px; height: 960px; }

  .card { position: absolute; width: 860px; height: 306px; }
  .card--front { left: 46px; top: 62px; background: var(--card-dark); }
  .card--back  { left: 288px; top: 476px; background: var(--card-light); }

  .rule { position: absolute; height: 1px; }

  /* Front */
  .front-mark {
    position: absolute; left: 378px; top: 22px;
    width: 120px; height: 120px; border-radius: 50%;
    background: var(--peach);
  }
  .front-studio {
    position: absolute; left: 0; width: 860px; text-align: center;
    color: var(--mark-grey); text-transform: uppercase;
  }
  .front-studio--line1 { top: 156px; font-size: 29px; letter-spacing: 5px; }
  .front-studio--line2 { top: 188px; font-size: 16px; letter-spacing: 5px; }
  .front .rule { left: 92px; width: 686px; background: var(--rule-dark); }
  .front-name {
    position: absolute; top: 215px; left: 0; width: 860px; text-align: center;
    color: var(--text-white); font-size: 27px;
  }
  .front-name .role { font-size: 22px; }
  .front-services {
    position: absolute; top: 258px; left: 0; width: 860px; text-align: center;
    color: var(--text-muted); font-size: 18px;
  }

  /* Back */
  .back .rule { left: 28px; width: 806px; background: var(--rule-light); }
  .back-mark {
    position: absolute; left: 72px; top: 50px;
    width: 100px; height: 100px; border-radius: 50%;
    background: var(--peach);
  }
  .back-studio {
    position: absolute; left: 22px; width: 200px; top: 164px;
    text-align: center; color: var(--peach); font-size: 14px;
    letter-spacing: 2px; text-transform: uppercase;
  }
  .back-divider {
    position: absolute; left: 299px; top: 43px; width: 3px; height: 174px;
    background: linear-gradient(to bottom, rgba(0,0,0,0.05), #1a1a1a 50%, rgba(0,0,0,0.05));
  }
  .contact-list { position: absolute; left: 325px; top: 72px; list-style: none; }
  .contact-list li { color: var(--text-ink); font-size: 21px; line-height: 41px; }
  .social {
    position: absolute; top: 239px; display: flex; align-items: center; gap: 18px;
    color: var(--text-ink); font-size: 22px;
  }
  .social--pictogram { left: 49px; }
  .social--friendwall { left: 495px; }
  .social-square { width: 30px; height: 30px; }
  .social--pictogram .social-square { background: var(--icon-a); }
  .social--friendwall .social-square { background: var(--icon-b); }
  .social-sep { position: absolute; left: 438px; top: 239px; font-size: 22px; color: var(--text-ink); }
</style>
</head>
<body>
<main class="canvas">

  <section class="card card--front front" aria-label="Card front">
    <div class="front-mark" aria-hidden="true"></div>
    <div class="front-studio front-studio--line1">Maris Dovey</div>
    <div class="front-studio front-studio--line2">Studio</div>
    <div class="rule" style="top:212px"></div>
    <div class="front-name">Tessa Varnold <span class="role">(Art and Design Consultant)</span></div>
    <div class="rule" style="top:248px"></div>
    <div class="front-services">Dealer | Curator | Events | Styling | Creative Sourcing</div>
    <div class="rule" style="top:286px"></div>
  </section>

  <section class="card card--back back" aria-label="Card back">
    <div class="rule" style="top:25px"></div>
    <div class="back-mark" aria-hidden="true"></div>
    <div class="back-studio">Maris Dovey Studio</div>
    <div class="back-divider" aria-hidden="true"></div>
    <ul class="contact-list">
      <li>Phone: 0438 217 604</li>
      <li>Email: tessa@marisdoveystudio.example</li>
      <li>Web: www.marisdoveystudio.example</li>
    </ul>
    <div class="rule" style="top:228px"></div>
    <div class="social social--pictogram"><span class="social-square" aria-hidden="true"></span>MarisDoveyAdviser</div>
    <div class="social-sep">|</div>
    <div class="social social--friendwall"><span class="social-square" aria-hidden="true"></span>marisdoveystudio</div>
    <div class="rule" style="top:278px"></div>
  </section>

</main>
</body>
</html>
```